Full Page Color Ad

We need a full page 8.5 x 11 ad created for a magazine. Please see the attached examples. It would be best if the wording/style stayed the same. As far as background image, we are looking for something catchy that portrays "hidden treasure". Please be sure to include the logos as well. If you have any questions or need anything else, please email mhorvent@tarquill.com You can also visit www.tarquill.com to learn at little about our company and see our branding/style.
*Please follow the style and wording of the examples as best as possible. Not looking for variation on the text layout- more ofthe background and added creativity.*
Industry/Entity Type
It Company
Look and feel

```html
<!DOCTYPE html>
<html lang="en">
<head>
<meta charset="utf-8">
<title>Discover Hidden Value – Tarquill Magazine Ad</title>
<link rel="stylesheet" href="https://fonts.googleapis.com/css2?family=Arimo:wght@400;700&family=Oswald:wght@600&display=swap">
<style>
  :root {
    --sea-light: #8fd0ef;
    --sea-mid: #1f6f9e;
    --sea-deep: #0b2c45;
    --sea-abyss: #0a1d2c;
    --gold: #f0ad1c;
    --navy-ink: #142a42;
    --white: #ffffff;
    --brand-blue: #1a4f9c;
    --badge-blue: #1f6fb8;
  }
  * { margin: 0; padding: 0; box-sizing: border-box; }
  html, body { width: 900px; height: 1200px; overflow: hidden; background: var(--sea-abyss); }
  .ad {
    position: relative;
    width: 900px;
    height: 1200px;
    overflow: hidden;
    font-family: "Arimo", Arial, sans-serif;
  }
  .ad__photo {
    position: absolute;
    inset: 0;
    background:
      radial-gradient(ellipse 340px 260px at 300px 340px, rgba(230,245,255,0.85), rgba(143,208,239,0) 70%),
      linear-gradient(180deg, var(--sea-light) 0%, var(--sea-mid) 22%, #14476d 45%, var(--sea-deep) 65%, var(--sea-abyss) 100%);
  }
  .headline-band {
    position: absolute;
    left: 0;
    top: 102px;
    width: 880px;
    height: 101px;
  }
  .headline-band svg { position: absolute; inset: 0; }
  .headline {
    position: absolute;
    left: 40px;
    top: 0;
    height: 101px;
    line-height: 101px;
    font-size: 76px;
    font-weight: 400;
    color: var(--navy-ink);
    letter-spacing: -0.5px;
    white-space: nowrap;
  }
  .headline strong { font-weight: 700; }
  .tagline {
    position: absolute;
    font-weight: 700;
    color: var(--gold);
    white-space: nowrap;
    line-height: 1;
  }
  .tagline--lead { left: 44px; top: 716px; font-size: 52px; }
  .tagline--end { left: 559px; top: 840px; font-size: 57px; }
  .process-list {
    position: absolute;
    left: 329px;
    top: 716px;
    list-style: none;
    font-family: "Oswald", Impact, sans-serif;
    font-weight: 600;
    font-size: 25px;
    line-height: 33px;
    color: var(--white);
    text-transform: uppercase;
    letter-spacing: 0.2px;
  }
  .process-list .is-highlight { color: var(--gold); }
  .brand-mark {
    position: absolute;
    left: 55px;
    top: 1073px;
    width: 82px;
    height: 84px;
    background: var(--brand-blue);
    color: var(--white);
    font-weight: 700;
    font-size: 15px;
    padding: 8px 0 0 5px;
  }
  .footer-copy {
    position: absolute;
    left: 165px;
    top: 1081px;
    width: 535px;
    font-size: 12.5px;
    line-height: 16.5px;
    color: var(--white);
  }
  .footer-url {
    position: absolute;
    left: 165px;
    top: 1151px;
    font-size: 15px;
    color: var(--white);
  }
  .partner-badge {
    position: absolute;
    left: 713px;
    top: 1073px;
    width: 138px;
    height: 87px;
    background: var(--badge-blue);
  }
</style>
</head>
<body>
  <main class="ad">
    <div class="ad__photo" role="img" aria-label="Underwater scene with sunlight rays streaming down through the ocean surface into deep blue water"></div>

    <header class="headline-band">
      <svg width="880" height="101" viewBox="0 0 880 101" aria-hidden="true">
        <polygon points="0,0 880,0 817,101 0,101" fill="var(--gold)"/>
      </svg>
      <h1 class="headline">Discover <strong>Hidden</strong> Value</h1>
    </header>

    <p class="tagline tagline--lead">From Your</p>
    <ul class="process-list">
      <li>Consolidations</li>
      <li>Financial Planning</li>
      <li>Strategy Management</li>
      <li>Profitability</li>
      <li class="is-highlight">Performance<br>Management</li>
      <li>Balanced Scorecard</li>
      <li>Sales &amp; Operations<br>Planning</li>
    </ul>
    <p class="tagline tagline--end">Process.</p>

    <footer>
      <div class="brand-mark">tarquill</div>
      <p class="footer-copy">Tarquill is trusted by more companies globally to deliver high value solutions featuring Veridex's Business Analytics portfolio. Our team offers visionary services that maximize the business value your company can realize from these powerful products. Contact us today for more information.</p>
      <p class="footer-url">www.tarquill.com</p>
      <div class="partner-badge" aria-hidden="true"></div>
    </footer>
  </main>
</body>
</html>
```